Varentoria Business Card and Letter Head

We are a leadership assessment consultancy based in Sydney, Australia. We help executive-level decison-makers select leaders for more senior level roles in corporate and government organisations. Our methodology is based on the latest research from the field of neuroscience.
We need a business card design and matching letter head that presents our company, Varentoria, as a:
1. trusted adviser to senior executive-level decison makers
2. niche consultancy who are experts in the field of assessing leadership talent
3. results-focused solution provider who balance scientific methods with pragmatic solutions
The following company details should be used in all designs:
Company Name: Varentoria
Details (for business card):
Derek Hanford
Prime Capacity Officer
Level 29, Marlow Tower
7 Marlow Square
Sydney, NSW 2000 Australia
Phone: 1300 582 714
Mobile: 0412 637 258
Email: derek.hanford@varentoria-example.com.au
Website: varentoria-example.com.au
I have attached the logo for Varentoria (for both a white and black background) - your business card and letter head designs must incoporate this logo and colour scheme.
Thanks for your interest in this project, I'm looking forward to receiving your ideas.
Regards,
Derek
Target Market(s)
Executive-level decison-makers in corporate and government organisations (e.g., CEO, VP, Head of Human Resources)
Industry/Entity Type
Leadership
Look and feel

```html
<!DOCTYPE html>
<html lang="en">
<head>
<meta charset="utf-8">
<title>Varentoria Business Card</title>
<link rel="stylesheet" href="https://fonts.googleapis.com/css2?family=Raleway:wght@700&family=Arimo:wght@400;700&family=Open+Sans:wght@400;700&display=swap">
<style>
  :root {
    --backdrop: #e9e7e4;
    --card: #ffffff;
    --ink: #3d3d3d;
    --accent: #b3261e;
    --shadow: rgba(0, 0, 0, 0.18);
  }
  * { box-sizing: border-box; margin: 0; padding: 0; }
  html, body {
    width: 1200px;
    height: 665px;
    overflow: hidden;
    background: var(--backdrop);
  }
  .stage {
    position: relative;
    width: 1200px;
    height: 665px;
  }
  .card {
    position: absolute;
    top: 188px;
    width: 500px;
    height: 290px;
    background: var(--card);
    border-radius: 26px;
    box-shadow: 0 6px 18px var(--shadow);
    overflow: hidden;
  }
  .card--front { left: 70px; }
  .card--back { left: 630px; }

  .brand {
    position: absolute;
    display: flex;
    align-items: center;
    gap: 12px;
    font-family: "Raleway", sans-serif;
    font-weight: 700;
    color: var(--ink);
    letter-spacing: -1px;
    line-height: 1;
  }
  .brand__mark {
    display: block;
    flex: none;
    background: var(--accent);
  }

  .card--front .brand { left: 40px; top: 40px; font-size: 52px; }
  .card--front .brand__mark { width: 22px; height: 22px; }

  .card--back .brand { left: 48px; top: 100px; font-size: 58px; }
  .card--back .brand__mark { width: 24px; height: 24px; }

  .person {
    position: absolute;
    left: 40px;
    top: 160px;
    font-family: "Open Sans", sans-serif;
    font-size: 14px;
    color: var(--accent);
  }
  .person__name { font-weight: 700; }
  .person__role { font-size: 12.5px; }

  .contact {
    position: absolute;
    left: 40px;
    top: 192px;
    list-style: none;
    font-family: "Arimo", sans-serif;
    font-size: 12px;
    color: var(--ink);
    line-height: 17px;
  }
  .contact__item { display: flex; align-items: center; gap: 5px; }
  .contact__icon { width: 11px; height: 11px; flex: none; }

  .address {
    position: absolute;
    right: 34px;
    top: 120px;
    font-family: "Arimo", sans-serif;
    font-style: normal;
    font-size: 12.5px;
    line-height: 20px;
    color: var(--ink);
    text-align: right;
  }

  .website {
    position: absolute;
    right: 34px;
    bottom: 38px;
    font-family: "Open Sans", sans-serif;
    font-size: 15px;
    letter-spacing: 0.4px;
    color: var(--ink);
  }
  .website__domain { color: var(--accent); font-weight: 700; }
</style>
</head>
<body>
<main class="stage">

  <section class="card card--front" aria-label="Business card front">
    <div class="brand"><span class="brand__mark"></span>Varentoria</div>

    <p class="person">
      <span class="person__name">Derek Hanford</span>
      <span class="person__role">&nbsp;/&nbsp;Prime Capacity Officer</span>
    </p>

    <ul class="contact">
      <li class="contact__item">
        <svg class="contact__icon" viewBox="0 0 12 12"><circle cx="6" cy="6" r="5.2" fill="none" stroke="var(--accent)" stroke-width="1.2"/><path d="M4 3.5 L5.2 3.5 L5.6 5 L4.9 5.6 Q5.6 7 6.9 7.4 L7.4 6.7 L8.8 7.1 L8.8 8.2 Q5 8.6 4 3.5Z" fill="var(--accent)"/></svg>
        1300 582 714
      </li>
      <li class="contact__item">
        <svg class="contact__icon" viewBox="0 0 12 12"><rect x="3.5" y="1" width="5" height="10" rx="1" fill="var(--accent)"/><rect x="4.4" y="2.3" width="3.2" height="4" fill="#fff"/></svg>
        0412 637 258
      </li>
      <li class="contact__item">
        <svg class="contact__icon" viewBox="0 0 12 12"><rect x="1" y="3" width="10" height="6.5" fill="var(--accent)"/><path d="M1 3 L6 6.8 L11 3" fill="none" stroke="#fff" stroke-width="1"/></svg>
        derek.hanford@varentoria-example.com.au
      </li>
      <li class="contact__item">
        <svg class="contact__icon" viewBox="0 0 12 12"><circle cx="6" cy="6" r="5" fill="var(--accent)"/><path d="M1 6 H11 M6 1 V11 M2 3.6 H10 M2 8.4 H10" stroke="#fff" stroke-width="0.8"/></svg>
        www.varentoria-example.com.au
      </li>
    </ul>

    <address class="address">
      Level 29, Marlow Tower<br>
      7 Marlow Square<br>
      Sydney,<br>
      NSW 2000 Australia
    </address>
  </section>

  <section class="card card--back" aria-label="Business card back">
    <div class="brand"><span class="brand__mark"></span>Varentoria</div>
    <p class="website">www.<span class="website__domain">varentoria-example</span>.com.au</p>
  </section>

</main>
</body>
</html>
```